I have written a book called "Whispers from the Back Office - Uncover the trade tricks advisers bill huge fees every season for and would rather keep hidden"

This book will be sold through this webpage as an ebook. i have attached a copy of the cover of the book and I would like the website to be consistent with the look and feel of the book cover.

Target Market(s)

Business owners

Industry/Entity Type

Business

Requirements
Must have
• There has been a video produced for the promotion of this book which is yet to be completed. The video will be on ClipNest and the video needs to be prominent on the homepage.

I need to be able to manage and change the content as I wish on the website eg wordpress.

The page will need have a Coinvey purchase button

Also a 100% money back guarantee sign

Nice to have
• Friendloop plug in to show how many people like the page

Should not have
• I don't want the homepage or any of the other pages to be too cluttered

```html
<!DOCTYPE html>
<html lang="en">
<head>
<meta charset="utf-8">
<title>Whispers from the Back Office</title>
<link href="https://fonts.googleapis.com/css2?family=Arvo&family=Open+Sans:wght@400;600&display=swap" rel="stylesheet">
<style>
:root{
  --blue:#12a7e6;
  --blue-dark:#0e86c7;
  --ink:#3a3a3a;
  --text:#555;
  --muted:#8a8a8a;
  --page:#f5f6f6;
  --panel:#fbfcfc;
  --line:#e6e8e8;
  --dark:#3b3f42;
  --gold:#f0b92a;
  --gold-light:#f8d45a;
}
*{box-sizing:border-box;margin:0;padding:0}
html,body{width:1186px;height:1200px;overflow:hidden}
body{background:var(--page);font-family:"Open Sans",sans-serif;color:var(--text);position:relative}
.abs{position:absolute}
.search{left:801px;top:57px;width:256px;height:25px;background:#eaebeb;border-radius:4px;font-size:10px;color:#c9cbcb;padding:6px 8px}
.search svg{position:absolute;right:8px;top:4px}
.logo{left:128px;top:91px;font-family:"Arvo",serif;font-weight:400;line-height:1}
.logo .top{font-size:26px;color:var(--ink)}
.logo .bottom{font-size:30px;color:var(--blue);letter-spacing:.5px;margin-top:1px}
.nav{left:565px;top:95px;height:62px;display:flex;font-size:15px;color:#555}
.nav a{display:block;padding:0 19px;line-height:66px;color:inherit;text-decoration:none}
.nav a.active{background:var(--blue);color:#fff;padding:0 21px}
.bar{left:128px;top:157px;width:929px;height:5px;background:var(--blue)}
.hero{left:128px;top:162px;width:929px;height:329px;background:radial-gradient(ellipse at 50% 30%,#fafafa 0%,#e9eaea 70%,#dfe0e0 100%)}
.video{left:99px;top:53px;width:424px;height:244px;background:linear-gradient(135deg,#d3ecf6,#f3f8e4 60%,#e6efd9)}
.video .cover{position:absolute;left:31px;top:30px;width:118px;height:167px;background:var(--blue)}
.video .presenter{position:absolute;left:232px;top:10px;width:160px;height:234px;background:linear-gradient(180deg,#c8d9ee,#7a9fd0);border-radius:40px 40px 0 0}
.play{position:absolute;left:180px;top:104px;width:64px;height:36px;background:#454545;border-radius:3px}
.play svg{position:absolute;left:26px;top:11px}
.controls{position:absolute;left:18px;top:206px;width:391px;height:26px;background:#3e4042;border-radius:3px}
.track{position:absolute;left:10px;top:10px;width:298px;height:6px;background:#777;border-radius:3px}
.track i{display:block;width:130px;height:6px;background:var(--blue);border-radius:3px}
.time{position:absolute;left:129px;top:-8px;font-size:8px;color:#333;background:#fff;padding:0 2px}
.controls .hd{position:absolute;left:350px;top:6px;font-size:9px;color:var(--blue);font-weight:600;font-style:italic}
.arrow{width:38px;height:38px;border-radius:50%;background:#fff;top:150px}
.arrow svg{position:absolute;left:12px;top:10px}
.hero-title{left:538px;top:50px;font-family:"Arvo",serif;font-weight:400;line-height:1}
.hero-title .top{font-size:26px;color:var(--ink)}
.hero-title .bottom{font-size:30px;color:var(--blue);margin-top:1px}
.hero-text{left:538px;top:120px;width:337px;font-size:12.2px;line-height:20px;text-align:justify;color:#555}
.btn{display:block;text-align:center;color:#fff;background:linear-gradient(#3aa0ec,#1c78d6);border:1px solid #1a6fc4;border-radius:2px;text-decoration:none}
.hero .btn{top:256px;width:114px;height:40px;line-height:38px;font-size:13px;font-weight:600}
.welcome{left:128px;top:528px;font-family:"Arvo",serif;font-weight:400;font-size:24px;color:var(--ink)}
.book{left:150px;top:576px;width:177px;height:251px;background:linear-gradient(160deg,#1eb0ec,#0ca2e2)}
.intro{left:346px;top:572px;width:712px;font-size:12.3px;line-height:20px;text-align:justify}
.intro p+p{margin-top:20px}
.card{top:866px;height:176px;background:var(--panel);border:1px solid var(--line)}
.brand{position:absolute;left:0;right:0;top:16px;text-align:center;font-size:44px;font-weight:600;color:#1f3f7a}
.cards{position:absolute;left:48px;top:96px;display:flex;gap:6px}
.cards span{width:47px;height:27px;background:#eef0f2;border:1px solid #d5d8dc;font-size:9px;font-weight:600;color:#444;display:flex;align-items:center;justify-content:center}
.card .btn{position:absolute;width:88px;height:23px;line-height:21px;font-size:10px;font-weight:600}
.badge{position:absolute;left:22px;top:28px;width:110px;height:100px;border-radius:50%;background:radial-gradient(circle at 50% 45%,var(--gold-light),var(--gold) 70%,#d79a1c)}
.guarantee{position:absolute;left:152px;top:44px;width:130px;font-size:10.5px;line-height:18px;color:var(--muted);text-align:justify}
.likes{font-size:10px;color:#333;position:absolute;left:18px;top:12px}
.faces{position:absolute;left:18px;top:38px;display:grid;grid-template-columns:repeat(5,50px);gap:3px}
.faces i{display:block;width:50px;height:50px}
.plugin{position:absolute;left:18px;right:18px;top:150px;border-top:1px solid #d4d6d8;padding-top:6px;font-size:9px;color:#5a6a8a;display:flex;align-items:center;gap:5px}
.plugin b{width:11px;height:11px;background:#3b5b98;display:block}
.footer{left:0;top:1095px;width:1186px;height:105px;background:#f9fafa}
.footer-nav{left:122px;top:1114px;font-size:12.3px;color:var(--muted);display:flex;gap:14px}
.footer-nav .sep{color:#999}
.copy{left:124px;top:1145px;font-size:12.3px;color:var(--muted)}
.social{left:880px;top:1115px;display:flex;gap:11px}
.social span{width:41px;height:41px;border-radius:50%;background:var(--dark);color:#fff;font-size:8px;display:flex;align-items:center;justify-content:center}
</style>
</head>
<body>
<div class="abs search">Search<svg width="16" height="16" viewBox="0 0 16 16"><circle cx="6.5" cy="6.5" r="5" fill="none" stroke="#fff" stroke-width="2"/><line x1="10" y1="10" x2="15" y2="15" stroke="#fff" stroke-width="2"/></svg></div>

<div class="abs logo"><div class="top">Whispers from the</div><div class="bottom">BACK OFFICE</div></div>

<nav class="abs nav">
  <a class="active" href="#">Home</a><a href="#">About Us</a><a href="#">Online sale</a><a href="#">Buy now</a><a href="#">Contact Us</a>
</nav>
<div class="abs bar"></div>

<section class="abs hero">
  <div class="abs arrow" style="left:17px"><svg width="12" height="18" viewBox="0 0 12 18"><path d="M10 2 3 9l7 7" fill="none" stroke="#ccc" stroke-width="2.5"/></svg></div>
  <div class="abs arrow" style="left:884px"><svg width="12" height="18" viewBox="0 0 12 18"><path d="M2 2l7 7-7 7" fill="none" stroke="#ccc" stroke-width="2.5"/></svg></div>
  <div class="abs video" aria-label="ClipNest promotional video player">
    <div class="cover" role="img" aria-label="Book cover thumbnail with a businessman silhouette"></div>
    <div class="presenter" role="img" aria-label="Author presenting the book, holding a notepad"></div>
    <div class="play"><svg width="13" height="14" viewBox="0 0 13 14"><path d="M0 0l13 7-13 7z" fill="#fff"/></svg></div>
    <div class="controls">
      <div class="track"><i></i><span class="time">00:34</span></div>
      <span class="hd">HD</span>
    </div>
  </div>
  <div class="abs hero-title"><div class="top">Whispers from the</div><div class="bottom">BACK OFFICE</div></div>
  <p class="abs hero-text">Lorem Ipsum is simply dummy text of the printing and typesetting industry. Lorem Ipsum has been the industry's standard dummy text ever since the 1500s, when an unknown printer took a galley &nbsp;Lorem Ipsum is simply dummy text of the printing and typesetting industry. Lorem Ipsum has been the industry's standard dummy .</p>
  <a class="abs btn" style="left:538px" href="#">Buy Now</a>
  <a class="abs btn" style="left:675px" href="#">Read More</a>
</section>

<h2 class="abs welcome">Welcome to e book</h2>
<div class="abs book" role="img" aria-label="Whispers from the Back Office book cover by Morgan Hale, with a speech banner and businessman silhouette"></div>
<div class="abs intro">
  <p>Lorem ipsum dolor sit amet, consectetur adipisicing elit, sed do eiusmod tempor incididunt ut labore et dolore magna aliqua. Ut enim ad minim veniam, quis nostrud exercitation ullamco laboris nisi ut aliquip ex ea commodo consequat. Duis aute irure dolor in reprehenderit in voluptate velit esse cillum dolore eu fugiat nulla pariatur. Excepteur sint occaecat cupidatat non proident, sunt in culpa qui officia deserunt mollit anim id est laborumLorem ipsum dolor sit amet, consectetur adipisicing elit, sed do eiusmod tempor incididunt ut labore et dolore magna aliqua. Ut enim ad minim veniam, quis nostrud exercitation ullamco laboris nisi ut aliquip ex ea commodo consequat. Duis aute irure dolor in reprehenderit in voluptate velit esse cillum dolore eu fugiat nulla pariatur.</p>
  <p>Excepteur sint occaecat cupidatat non proident, sunt in culpa qui officia deserunt mollit anim id est laborumLorem ipsum dolor sit amet, consectetur adipisicing elit, sed do eiusmod tempor incididunt ut labore et dolore magna aliqua. Ut enim ad minim veniam, quis nostrud exercitation ullamco laboris nisi ut aliquip ex ea commodo consequat. Duis aute irure dolor in reprehenderit in voluptate velit esse cillum dolore eu fugiat nulla pariatur. Excepteur sint occaecat cupidatat non proident, sunt in culpa qui officia deserunt mollit anim id est laborumLorem ipsum dolor sit amet</p>
</div>

<div class="abs card" style="left:128px;width:297px">
  <div class="brand">Coinvey</div>
  <div class="cards"><span>Orbex</span><span>Vantix</span><span>Merra</span><span>Findly</span></div>
  <a class="btn" style="left:110px;top:137px" href="#">Buy Now</a>
</div>

<div class="abs card" style="left:443px;width:297px">
  <div class="badge" role="img" aria-label="100% money back guarantee seal"></div>
  <p class="guarantee">Sed ut perspiciatis unde omnis iste natus error sit voluptatem accusantium dolorem quetotam</p>
  <a class="btn" style="left:158px;top:137px" href="#">Read More</a>
</div>

<div class="abs card" style="left:761px;width:306px;background:#fff">
  <div class="likes">22,272 people like</div>
  <div class="faces">
    <i role="img" aria-label="Fan profile photo" style="background:#8a9aa8"></i>
    <i role="img" aria-label="Fan profile photo" style="background:#9b8f86"></i>
    <i role="img" aria-label="Fan profile photo" style="background:#7a4a3a"></i>
    <i role="img" aria-label="Fan profile photo" style="background:#d9d9d9"></i>
    <i role="img" aria-label="Fan profile photo" style="background:#eee"></i>
    <i role="img" aria-label="Fan profile photo" style="background:#6c7a5c"></i>
    <i role="img" aria-label="Fan profile photo" style="background:#5a6a3a"></i>
    <i role="img" aria-label="Fan profile photo" style="background:#d8cfc4"></i>
    <i role="img" aria-label="Fan profile photo" style="background:#3e4a3a"></i>
    <i role="img" aria-label="Fan profile photo" style="background:#4a4a4a"></i>
  </div>
  <div class="plugin"><b></b>Friendloop social plugin</div>
</div>

<div class="abs footer"></div>
<div class="abs footer-nav"><span>Home</span><span class="sep">|</span><span>About Us</span><span class="sep">|</span><span>Online sale</span><span class="sep">|</span><span>Buy now</span><span class="sep">|</span><span>Contact Us</span></div>
<div class="abs copy">© 2013 Whispers from the back office ,All &nbsp;rights reserved</div>
<div class="abs social"><span>Chirpa</span><span>Friendloop</span><span>Circlo</span><span>Feed</span></div>
</body>
</html>
```